We need a business card design, letterhead design and envelope design for our corporate image

We are looking for a corporate business card design, letterhead and envelope design to match the business card design. Logo is done.

```html
<!DOCTYPE html>
<html lang="en">
<head>
<meta charset="UTF-8">
<title>Veltrax Business Card</title>
<link href="https://fonts.googleapis.com/css2?family=Open+Sans:wght@400;700;800&display=swap" rel="stylesheet">
<style>
  :root {
    --backdrop: #2a2a2a;
    --card: #1b1b1b;
    --pattern-light: #222222;
    --pattern-dark: #161616;
    --accent: #f7c614;
    --ink: #ffffff;
  }
  html, body {
    margin: 0;
    padding: 0;
    width: 1200px;
    height: 900px;
    overflow: hidden;
    background: var(--backdrop);
    font-family: "Open Sans", Arial, sans-serif;
  }
  .card {
    position: absolute;
    left: 250px;
    width: 700px;
    height: 400px;
    background: var(--card);
    box-shadow: 0 16px 40px rgba(0,0,0,0.5);
    overflow: hidden;
  }
  .card-front { top: 40px; }
  .card-back { top: 460px; }

  /* Front */
  .holder-name {
    position: absolute;
    left: 48px;
    top: 44px;
    margin: 0;
    color: var(--accent);
    font-size: 24px;
    font-weight: 800;
    line-height: 1.2;
    letter-spacing: 0.4px;
    text-transform: uppercase;
  }
  .holder-title {
    position: absolute;
    left: 48px;
    top: 78px;
    margin: 0;
    color: var(--ink);
    font-size: 16px;
    font-weight: 400;
    line-height: 1.2;
  }
  .divider {
    position: absolute;
    left: 48px;
    top: 122px;
    width: 604px;
    height: 2px;
    background: var(--accent);
  }
  .contact-list {
    position: absolute;
    left: 48px;
    top: 140px;
    margin: 0;
    padding: 0;
    list-style: none;
  }
  .contact-item {
    display: flex;
    align-items: center;
    gap: 10px;
    height: 27px;
    color: var(--ink);
    font-size: 15px;
  }
  .contact-icon {
    width: 14px;
    height: 14px;
    flex: none;
  }
  .brand {
    position: absolute;
    display: flex;
    align-items: center;
    gap: 12px;
  }
  .card-front .brand {
    right: 48px;
    top: 40px;
  }
  .brand-square {
    width: 26px;
    height: 26px;
    background: var(--accent);
  }
  .brand-name {
    color: var(--ink);
    font-size: 48px;
    font-weight: 700;
    line-height: 1;
  }
  .address {
    position: absolute;
    right: 48px;
    bottom: 46px;
    margin: 0;
    color: var(--ink);
    font-size: 16px;
    font-style: normal;
    line-height: 1.5;
    text-align: right;
  }
  .base-band {
    position: absolute;
    left: 0;
    bottom: 0;
    width: 100%;
    height: 9px;
    background: var(--accent);
  }

  /* Back */
  .back-pattern {
    position: absolute;
    inset: 0;
    background: linear-gradient(135deg, var(--pattern-light), var(--pattern-dark));
  }
  .card-back .brand {
    left: 50%;
    top: 50%;
    transform: translate(-50%, -50%);
  }
</style>
</head>
<body>
  <section class="card card-front">
    <h1 class="holder-name">Daniel Arvest</h1>
    <p class="holder-title">President</p>

    <div class="brand">
      <span class="brand-square"></span>
      <span class="brand-name">Veltrax</span>
    </div>

    <div class="divider"></div>

    <ul class="contact-list">
      <li class="contact-item">
        <svg class="contact-icon" viewBox="0 0 24 24" aria-hidden="true">
          <path fill="var(--accent)" d="M6.6 10.8a15.1 15.1 0 0 0 6.6 6.6l2.2-2.2a1 1 0 0 1 1-.25 11.4 11.4 0 0 0 3.6.57 1 1 0 0 1 1 1V20a1 1 0 0 1-1 1A17 17 0 0 1 3 4a1 1 0 0 1 1-1h3.5a1 1 0 0 1 1 1c0 1.25.2 2.450 .57 3.57a1 1 0 0 1-.25 1z"/>
        </svg>
        <span>555-310-4827</span>
      </li>
      <li class="contact-item">
        <svg class="contact-icon" viewBox="0 0 24 24" aria-hidden="true">
          <rect x="2" y="5" width="20" height="14" fill="var(--accent)"/>
          <path d="M2 5l10 8 10-8" fill="none" stroke="var(--card)" stroke-width="2"/>
        </svg>
        <span>darvest@veltrax.com</span>
      </li>
      <li class="contact-item">
        <svg class="contact-icon" viewBox="0 0 24 24" aria-hidden="true">
          <circle cx="12" cy="12" r="10" fill="none" stroke="var(--accent)" stroke-width="2.5"/>
          <path d="M2 12h20M12 2c3 3 3 17 0 20M12 2c-3 3-3 17 0 20" fill="none" stroke="var(--accent)" stroke-width="1.8"/>
        </svg>
        <span>www.veltrax.com</span>
      </li>
    </ul>

    <address class="address">
      1820 Harbor View Lane<br>
      Seacliff CA 90210
    </address>

    <div class="base-band"></div>
  </section>

  <section class="card card-back">
    <div class="back-pattern" role="img" aria-label="Tonal embossed repeat pattern of the brand mark covering the card back"></div>
    <div class="brand">
      <span class="brand-square"></span>
      <span class="brand-name">Veltrax</span>
    </div>
  </section>
</body>
</html>
```